Natural Light/Organic/Documentary Photography Business

I like a simple, approachable, feminine, earthy/organic feel. Earth/neutral tones, nothing too loud or obnoxious. I like the watercolor look. I don't want anything too trendy or something I'll get tired of after a couple months. As far as colors, I am much more a fan of cream/taupe/blue/green...not a fan of pink or purple at all.

Target Market(s)

Weddings & Families

Industry/Entity Type

Wedding Photography

Contact Information for Business Card

website, email, phone number

Font styles to use
Other font styles liked:
• Horizontes, Gotham

Colors

Designer to choose colors to be used in the design.

Requirements
Must have
• Website: www.mirelhatchway.com
• Phone: 418.629.5073
• Email: mirel@mirelhatchway.com
Nice to have
• I like the watercolor look but its not necessary. I like simple/earthy tones. Nothing too loud or distracting. Simple & feminine without being too girly. I like an approachable/soft feel.
• Instagram: www.instagram.com/mirelhatchwayphotography/
Should not have
• NO loud colors or design or pattern. I do not want a photo of a camera or lens or anything cheesy like that.

```html
<!DOCTYPE html>
<html lang="en">
<head>
<meta charset="utf-8">
<title>Mirel Hatchway Photography — Business Card</title>
<link href="https://fonts.googleapis.com/css2?family=Lato:wght@300;400&display=swap" rel="stylesheet">
<style>
  :root {
    --backdrop: #8c8c8c;
    --card-front-band: #ffffff;
    --card-back: #efefef;
    --ink: #3b3633;
    --taupe: #8a7d75;
    --tag: #9c948f;
    --rule: #9a918b;
    --peach: #e9c0a4;
    --cream: #e4dfda;
    --sage-sky: #b8d9cf;
  }
  * { box-sizing: border-box; margin: 0; padding: 0; }
  html, body {
    width: 1200px; height: 1200px; overflow: hidden;
    background: var(--backdrop);
    font-family: "Lato", Arial, sans-serif;
  }
  .canvas { position: relative; width: 1200px; height: 1200px; }
  .card {
    position: absolute; top: 310px; height: 593px;
    box-shadow: 2px 3px 6px rgba(0,0,0,0.35);
    overflow: hidden;
  }
  .card--front { left: 235px; width: 363px; background: var(--card-front-band); }
  .card--back { left: 628px; width: 367px; background: var(--card-back); }

  .wash {
    position: absolute; left: 0; width: 100%;
    background: linear-gradient(120deg, var(--peach) 0%, var(--cream) 50%, var(--sage-sky) 100%);
  }
  .card--front .wash { top: 0; height: 467px; }
  .card--back .wash { bottom: 0; height: 126px; }

  .wordmark { position: absolute; left: 0; width: 100%; text-align: center; color: var(--taupe); }
  .wordmark__name { font-weight: 300; font-size: 36px; letter-spacing: 1px; line-height: 1; }
  .wordmark__tag { font-weight: 400; font-size: 8px; letter-spacing: 4px; margin-top: 6px; line-height: 1; color: var(--tag); }
  .card--front .wordmark { top: 498px; }
  .card--back .wordmark { top: 120px; }

  .rule { position: absolute; left: 112px; width: 150px; height: 1px; background: var(--rule); }
  .rule--top { top: 206px; }
  .rule--bottom { top: 335px; }

  .contact {
    position: absolute; top: 234px; left: 0; width: 100%;
    text-align: center; color: var(--ink); font-style: normal;
    font-size: 19px; line-height: 24.5px; font-weight: 400;
  }
  .social {
    position: absolute; top: 366px; left: 0; width: 100%;
    display: flex; justify-content: center; align-items: center; gap: 9px;
    color: var(--ink); font-size: 17px;
  }
  .social__dot { width: 22px; height: 22px; border: 1.5px solid var(--taupe); border-radius: 50%; }
</style>
</head>
<body>
<main class="canvas">
  <section class="card card--front">
    <div class="wash" role="img" aria-label="Watercolor wash artwork in peach, cream, sage green and sky blue"></div>
    <div class="wordmark">
      <p class="wordmark__name">Mirel Hatchway</p>
      <p class="wordmark__tag">PHOTOGRAPHY</p>
    </div>
  </section>

  <section class="card card--back">
    <div class="wordmark">
      <p class="wordmark__name">Mirel Hatchway</p>
      <p class="wordmark__tag">PHOTOGRAPHY</p>
    </div>
    <div class="rule rule--top"></div>
    <address class="contact">
      418.629.5073<br>
      mirel@mirelhatchway.com<br>
      www.mirelhatchway.com
    </address>
    <div class="rule rule--bottom"></div>
    <p class="social"><span class="social__dot"></span>mirelhatchwayphotography</p>
    <div class="wash" role="img" aria-label="Strip of watercolor wash artwork in peach, cream, sage green and sky blue"></div>
  </section>
</main>
</body>
</html>
```